Corvane Holdings , new business card design

investment firm with corporate clients . need double sided business card , vertical and horizontal options ,logo must be clear. prefer pantone colors only and sharp design. website also www.corvane.ae

Khalid Bin Tarrafi
Managing Director
Tel. +971 4 387 2940
Mobile +971 50 518 2403
khalid@corvane.ae
Q-Span Plaza, officw 18-B07, Warqa Gardens, Dubai

Contact Information for Business Card

Khalid Bin Tarrafi
Managing Director

Font styles to use
Serif

Colors

Designer to choose colors to be used in the design.

```html
<!DOCTYPE html>
<html lang="en">
<head>
<meta charset="utf-8">
<title>Corvane Holdings – Business Card</title>
<link rel="stylesheet" href="https://fonts.googleapis.com/css2?family=Raleway:wght@300;400;700&display=swap">
<style>
  :root {
    --navy: #243f63;
    --white: #ffffff;
    --steel: #8c8f94;
    --brand-blue: #2e4d78;
    --backdrop: #e6e3e0;
    --ink-soft: #dfe6ef;
  }
  * { margin: 0; padding: 0; box-sizing: border-box; }
  html, body {
    width: 1200px; height: 997px; overflow: hidden;
    background: var(--backdrop);
    font-family: "Raleway", sans-serif;
  }
  .canvas { position: relative; width: 1200px; height: 997px; }

  .card {
    position: absolute;
    width: 560px; height: 320px;
    overflow: hidden;
    box-shadow: 0 2px 6px rgba(0,0,0,0.12);
  }

  /* Front side */
  .card--front { left: 60px; top: 110px; background: var(--white); }
  .front__brand {
    position: absolute; left: 32px; top: 66px;
    width: 190px;
    display: flex; align-items: center; gap: 10px;
  }
  .brand-square { width: 12px; height: 12px; background: var(--brand-blue); flex: none; }
  .brand-name {
    font-weight: 400; font-size: 20px; line-height: 1.2; letter-spacing: 3px;
    color: var(--brand-blue); text-transform: uppercase;
  }
  .brand-name span { display: block; }
  .front__web {
    position: absolute; left: 32px; bottom: 32px;
    font-size: 14px; letter-spacing: 4px; color: var(--navy); font-weight: 700;
  }
  .front__divider { position: absolute; left: 224px; top: 0; width: 40px; height: 320px; }
  .front__panel {
    position: absolute; left: 238px; top: 0; right: 0; bottom: 0;
    background: var(--navy); color: var(--white);
    padding: 34px 0 0 42px;
  }
  .holder__name { font-weight: 700; font-size: 17px; }
  .holder__title { font-weight: 300; font-size: 13px; margin-top: 3px; color: var(--ink-soft); }
  .holder__address {
    margin-top: 58px; font-weight: 300; font-size: 12.5px; line-height: 1.45; color: var(--ink-soft);
  }
  .contact-list { list-style: none; margin-top: 18px; }
  .contact-list li {
    display: flex; align-items: center; gap: 8px;
    font-weight: 300; font-size: 12.5px; line-height: 1.55; color: var(--ink-soft);
  }
  .contact-list svg { width: 11px; height: 11px; flex: none; }

  /* Back side */
  .card--back { left: 580px; top: 560px; background: var(--navy); }
  .back__brand {
    position: absolute; left: 0; right: 0; top: 0; bottom: 0;
    display: flex; align-items: center; justify-content: center; gap: 14px;
  }
  .back__brand .brand-square { background: var(--white); width: 14px; height: 14px; }
  .back__brand .brand-name { color: var(--white); font-size: 28px; letter-spacing: 4px; }
</style>
</head>
<body>
<main class="canvas">

  <section class="card card--front" aria-label="Business card front">
    <div class="front__brand">
      <span class="brand-square"></span>
      <span class="brand-name"><span>Corvane</span><span>Holdings</span></span>
    </div>
    <p class="front__web">www.corvane.ae</p>

    <svg class="front__divider" viewBox="0 0 40 320" aria-hidden="true">
      <rect x="6" y="0" width="10" height="320" fill="#8c8f94"/>
      <polygon points="14,26 28,40 14,54" fill="#8c8f94"/>
    </svg>

    <div class="front__panel">
      <h1 class="holder__name">Khalid Bin Tarrafi</h1>
      <p class="holder__title">Managing Director</p>
      <p class="holder__address">Q-Span Plaza, officw 18-B07,<br>Warqa Gardens, Dubai</p>
      <ul class="contact-list">
        <li>
          <svg viewBox="0 0 12 12"><path d="M2.5 1 L4.5 1 L5.2 3.5 L4 4.6 Q5 7 7.4 8 L8.5 6.8 L11 7.5 L11 9.5 Q11 11 9.5 11 Q1 10 1 2.5 Q1 1 2.5 1Z" fill="#ffffff"/></svg>
          <span>+971 4 387 2940</span>
        </li>
        <li>
          <svg viewBox="0 0 12 12"><rect x="2" y="1" width="8" height="10" rx="1" fill="none" stroke="#ffffff" stroke-width="1.2"/></svg>
          <span>+971 50 518 2403</span>
        </li>
        <li>
          <svg viewBox="0 0 12 12"><rect x="1" y="2.5" width="10" height="7" fill="#ffffff"/><path d="M1 2.5 L6 6.5 L11 2.5" fill="none" stroke="#243f63" stroke-width="1"/></svg>
          <span>khalid@corvane.ae</span>
        </li>
      </ul>
    </div>
  </section>

  <section class="card card--back" aria-label="Business card back">
    <div class="back__brand">
      <span class="brand-square"></span>
      <span class="brand-name">Corvane Holdings</span>
    </div>
  </section>

</main>
</body>
</html>
```